Quick Straightforward Billboard Redesign

- Design billboard sized for 10 foot' x 36' foot width live area size and please include bleeds 6" around all sides
- Exact blue color match is imperative in headline, logo, phone number bubble or wherever used. C-83 / M-45 / Y-1 / K-0-
- What I hope to illustrate is that our company offers the best porch screening in the area area, in regards to quality, expertise, durability, storms proof, but we do not build screen porches.
- Current board is attached below from previous designer, and as you can see sizing was off, white space on edges make it appear to be sized incorrectly.
- I also attached my own little mock up idea well well if it helps, favorite image, logo, headline, etc and ideas perhaps on expanding or making this better?

Thanks so much!

Target Market(s)

Drivers and passengers, Southeastern NC, are of immense new construction and high end homes.

Industry/Entity Type

Construction

Colors
0054AA
0677BA
7BADD7
CADEEF
E8F1F8

Requirements
Must have
• Blue color matching
Nice to have
• Design spins or other thoughts on my little mock up

```html
<!DOCTYPE html>
<html lang="en">
<head>
<meta charset="UTF-8">
<title>Tidewater Screening Billboard</title>
<link href="https://fonts.googleapis.com/css2?family=Poppins:wght@700;800&family=Oswald:wght@600&display=swap" rel="stylesheet">
<style>
  :root {
    --brand-blue: #2f68a6;
    --brand-green: #2fa84f;
    --board-white: #f7f7f5;
    --page-bg: #e9edf1;
    --photo-sky: #8fb6dc;
    --photo-porch: #d9d6cf;
    --photo-furniture: #6a5f55;
    --text-light: #ffffff;
  }
  * { margin: 0; padding: 0; box-sizing: border-box; }
  html, body {
    width: 1200px;
    height: 645px;
    overflow: hidden;
    background: var(--page-bg);
  }
  .billboard {
    position: absolute;
    left: 20px;
    top: 161px;
    width: 1160px;
    height: 322px;
    background: var(--board-white);
    overflow: hidden;
  }
  .headline {
    position: absolute;
    left: 36px;
    top: 18px;
    font-family: 'Poppins', sans-serif;
    font-weight: 800;
    font-size: 60px;
    line-height: 64px;
    letter-spacing: 1px;
    text-transform: uppercase;
  }
  .headline-top { color: var(--brand-blue); display: block; }
  .headline-bottom { color: var(--brand-green); display: block; }
  .porch-photo {
    position: absolute;
    right: 0;
    top: 0;
    width: 470px;
    height: 100%;
    background:
      linear-gradient(180deg, var(--photo-porch) 0%, var(--photo-porch) 18%, var(--photo-sky) 24%, #a7c7a0 40%, #7b9a6b 48%, var(--photo-porch) 60%, var(--photo-furniture) 85%, #4d453e 100%);
    clip-path: polygon(40px 0, 100% 0, 100% 100%, 0 100%);
  }
  .brand {
    position: absolute;
    left: 38px;
    top: 212px;
    display: flex;
    align-items: center;
    gap: 16px;
  }
  .brand-mark {
    width: 62px;
    height: 62px;
    background: var(--brand-blue);
  }
  .brand-name {
    font-family: 'Oswald', sans-serif;
    font-weight: 600;
    font-size: 34px;
    line-height: 36px;
    color: var(--brand-blue);
    text-transform: uppercase;
  }
  .phone-band {
    position: absolute;
    left: 300px;
    top: 222px;
    width: 450px;
    height: 72px;
  }
  .phone-band-accent {
    position: absolute;
    left: 0;
    top: 0;
    width: 48px;
    height: 100%;
    background: var(--brand-green);
    clip-path: polygon(18px 0, 100% 0, 30px 100%, 0 100%);
  }
  .phone-band-body {
    position: absolute;
    left: 30px;
    top: 0;
    width: 420px;
    height: 100%;
    background: var(--brand-blue);
    clip-path: polygon(18px 0, 100% 0, 100% 100%, 0 100%);
    display: flex;
    align-items: center;
    justify-content: center;
  }
  .phone-number {
    font-family: 'Poppins', sans-serif;
    font-weight: 700;
    font-size: 46px;
    color: var(--text-light);
    letter-spacing: 1px;
  }
</style>
</head>
<body>
  <div class="billboard">
    <h1 class="headline">
      <span class="headline-top">Screen Your Porch</span>
      <span class="headline-bottom">Built for the Coast.</span>
    </h1>

    <div class="porch-photo" role="img" aria-label="Screened covered porch with wicker seating, ceiling fan and a lake view"></div>

    <div class="brand">
      <div class="brand-mark"></div>
      <div class="brand-name">Tidewater<br>Screening</div>
    </div>

    <div class="phone-band">
      <div class="phone-band-accent"></div>
      <div class="phone-band-body">
        <span class="phone-number">910.555.0142</span>
      </div>
    </div>
  </div>
</body>
</html>
```